Fitness Centre/Personal Trainer Business Card

We need a business card design for a company based in Singapore called 'Vigor Ledger'.

We are a team of Personal Trainers and we are planning to open our new training facility.

This design will also be printed/painted on the walls in our gym.

We are a new breed of personal trainers who take fitness seriously and holistically. We do not merely train our clients to be big and muscular.

We believe in wholeness. In our opinion, fitness should include: strength, speed, flexibility, mobility, stamina & agility. These are what we train for. Of course, nutrition/diet is key.

We use fitness tools such as kettlebells, QVL, Pylometric boxes, battling ropes, clubbells, medicine balls, bulgarian bags etc - functional and non-bulky tools.

I currently have a Facebook page 'Vigor Ledger SG' which shows a logo of a kettlebell. But my business focus has since changed.

Services provided:
- Kettlebell Sport Preparation
- Calisthenics Training
- Corrective Exercises
- Sports Strength & Conditioning
- 28 days Weight Loss Program
- Myofascial Rehab Therapy
- Sports/Thai Massage

Main colors for the design should be BLACK & YELLOW. We envision a design which is able to protray the holistic view we take on fitness. Also it should somewhat appeal to the ladies and not intimidate them.

Target Market(s)

People between 18-35 years old. Students and working class alike.

Industry/Entity Type

Training

Requirements
Must have
• Name: Marcus Obadiah Lim
Fitness Coach
Corrective Exercise Specialist
M: +65 9437 2065
E: marcus@sgvigorledger-example.com

Double-sided please.
Nice to have
• "What is your vigor ledger?"

```html
<!DOCTYPE html>
<html lang="en">
<head>
<meta charset="utf-8">
<title>Vigor Ledger – Business Card</title>
<link rel="stylesheet" href="https://fonts.googleapis.com/css2?family=Arimo:wght@400;700&family=Audiowide&display=swap">
<style>
  :root {
    --ink: #000000;
    --sun: #fff200;
    --paper: #ffffff;
    --shade: #3a3a2a;
  }
  * { margin: 0; padding: 0; box-sizing: border-box; }
  html, body { width: 900px; height: 1200px; overflow: hidden; background: var(--paper); }
  .canvas { position: relative; width: 900px; height: 1200px; background: var(--paper); font-family: "Arimo", Arial, sans-serif; color: var(--ink); }

  .card { position: absolute; left: 11px; width: 878px; background: var(--sun); overflow: hidden; }
  .card--front { top: 81px; height: 516px; }
  .card--back { top: 605px; height: 513px; }

  .front__band { position: absolute; left: 0; top: 0; width: 100%; height: 169px; background: var(--ink); }
  .brand { position: absolute; right: 50px; top: 62px; font-family: "Audiowide", sans-serif; font-size: 46px; line-height: 50px; color: var(--sun); text-transform: uppercase; text-align: right; letter-spacing: 1px; }

  .runner-art { position: absolute; left: 514px; top: 300px; width: 270px; height: 196px; border-radius: 40% 30% 45% 35%; background: radial-gradient(ellipse at center, var(--shade) 0%, rgba(58,58,42,0.55) 55%, rgba(255,242,0,0) 100%); }

  .contact { position: absolute; left: 26px; top: 395px; }
  .contact__name { font-size: 21px; font-weight: 700; line-height: 26px; }
  .contact__line { font-size: 18px; line-height: 24px; }

  .services { position: absolute; left: 40px; top: 153px; width: 322px; text-align: center; }
  .services__title { font-size: 21px; font-weight: 700; line-height: 28px; margin-bottom: 6px; }
  .services__item { font-size: 19px; line-height: 33.8px; }

  .bell-art { position: absolute; left: 445px; top: 35px; width: 380px; height: 440px; border-radius: 46% 46% 48% 48% / 40% 40% 56% 56%; background: var(--paper); }

  .tagline { position: absolute; left: 436px; top: 255px; font-family: "Audiowide", sans-serif; color: var(--ink); }
  .tagline span { display: block; line-height: 1; }
  .tagline__what { font-size: 38px; }
  .tagline__is { font-size: 26px; margin-left: 74px; margin-top: 2px; }
  .tagline__vigor { font-size: 54px; margin-left: 38px; margin-top: 4px; }
  .tagline__ledger { font-size: 54px; margin-left: 116px; margin-top: 2px; }
</style>
</head>
<body>
<div class="canvas">
  <section class="card card--front">
    <div class="front__band"></div>
    <div class="brand">Vigor<br>Ledger</div>
    <div class="runner-art" role="img" aria-label="Sketch of a sprinting athlete"></div>
    <div class="contact">
      <p class="contact__name">Marcus Obadiah Lim</p>
      <p class="contact__line">Fitness Coach &amp; Corrective Exercise Specialist</p>
      <p class="contact__line">Mob: +65 9437 2065</p>
      <p class="contact__line">Email: marcus@sgvigorledger-example.com</p>
    </div>
  </section>

  <section class="card card--back">
    <div class="services">
      <p class="services__title">- Services provided -</p>
      <p class="services__item">Kettlebell Sport Preparation,</p>
      <p class="services__item">Calisthenics Training,</p>
      <p class="services__item">Corrective Exercises,</p>
      <p class="services__item">Sports Strength &amp; Conditioning,</p>
      <p class="services__item">28 days Weight Loss Program,</p>
      <p class="services__item">Myofascial Rehab Therapy,</p>
      <p class="services__item">Sports/Thai Massage.</p>
    </div>
    <div class="bell-art" role="img" aria-label="Large white kettlebell silhouette"></div>
    <p class="tagline">
      <span class="tagline__what">What</span>
      <span class="tagline__is">is your</span>
      <span class="tagline__vigor">vigor</span>
      <span class="tagline__ledger">ledger?</span>
    </p>
  </section>
</div>
</body>
</html>
```